Mobile Fitness snd Therapy Business Card Design

I need a business card designed for my mobile fitness and therapy business.

Please view the images that I have uploaded. I like the simplicity of the design that I have attached. I adapted it with my information

Target Market(s)

Those seeking personal training, injury rehabilitation or massage therapy.

Industry/Entity Type

Business

Contact Information for Business Card

Derek Fulham - MSc, CAT(C), RMT, CSCS, Pn2
e-mail: derek@vantrelo.com
website: www.vantrelo.com
instagram: @derek_fulham

Font styles to use
Sans Serif

Colors
3176b5
0355a3

Requirements
Must have
• "Contact us to receive a FREE assessment"
• Services offered:
• Personal Training
• Golf Fitness
• Injury Rehab
• Massage Therapy
• Yoga
Nice to have
• Consistent colours with brand
• - Dark Blue: #232837
• - Blue: #5096f0
• Consistent look/feel with the website: www.vantrelo.com

```html
<!DOCTYPE html>
<html lang="en">
<head>
<meta charset="utf-8">
<title>Vantrelo Business Card</title>
<link href="https://fonts.googleapis.com/css2?family=Arimo:wght@400;700&display=swap" rel="stylesheet">
<style>
  :root{
    --ink:#232837;
    --blue:#5096f0;
    --deep-blue:#2a5fd6;
    --soft-blue:#86b8f6;
    --text:#2b2f3a;
    --paper:#ffffff;
    --backdrop:#e9eaec;
  }
  *{margin:0;padding:0;box-sizing:border-box}
  html,body{width:1200px;height:900px;overflow:hidden;background:var(--backdrop);font-family:"Arimo",Arial,sans-serif}
  .canvas{position:relative;width:1200px;height:900px}
  .card{position:absolute;left:320px;width:560px;height:320px;overflow:hidden;box-shadow:0 6px 18px rgba(0,0,0,.18)}
  .card-front{top:100px;background:var(--ink);display:flex;flex-direction:column;align-items:center;justify-content:center}
  .brand{display:flex;align-items:center;gap:14px}
  .brand-mark{width:16px;height:16px;background:var(--blue)}
  .brand-name{color:#fff;font-weight:700;font-size:52px;letter-spacing:6px;line-height:1}
  .tagline{margin-top:10px;color:#fff;font-weight:700;font-size:15px;letter-spacing:4.5px}
  .card-back{top:480px;background:linear-gradient(180deg,#fbfbfc,#eef0f2)}
  .edge-bar-left{position:absolute;left:0;top:78px;width:9px;height:172px;background:var(--soft-blue)}
  .edge-bar-right{position:absolute;right:0;top:22px;width:9px;height:92px;background:var(--deep-blue)}
  .identity{position:absolute;left:40px;top:92px}
  .person-name{color:var(--deep-blue);font-weight:700;font-size:22px;letter-spacing:.3px}
  .credentials{color:var(--blue);font-size:15px;margin-top:3px}
  .contact-list{list-style:none;margin-top:16px}
  .contact-list li{display:flex;align-items:center;gap:7px;color:var(--text);font-size:17px;line-height:25px}
  .contact-list svg{flex:none}
  .divider{position:absolute;left:350px;top:44px;width:4px;height:128px;background:var(--blue)}
  .services{position:absolute;left:372px;top:34px}
  .services-title{color:var(--blue);font-weight:700;font-size:14px;letter-spacing:.3px}
  .services-list{list-style:none;margin-top:14px}
  .services-list li{display:flex;align-items:center;gap:7px;color:var(--text);font-size:13px;line-height:17px}
  .service-bullet{flex:none;width:6px;height:6px;background:var(--blue)}
  .cta-band{position:absolute;left:0;bottom:0;width:100%;height:70px;background:var(--ink);display:flex;align-items:center;justify-content:center}
  .cta{color:var(--blue);font-weight:700;font-size:19px;letter-spacing:.4px}
</style>
</head>
<body>
<main class="canvas">
  <section class="card card-front">
    <div class="brand">
      <span class="brand-name">VANTRELO</span>
      <span class="brand-mark"></span>
    </div>
    <p class="tagline">NUTRITION - FITNESS - HEALTH</p>
  </section>

  <section class="card card-back">
    <span class="edge-bar-left"></span>
    <span class="edge-bar-right"></span>

    <div class="identity">
      <h1 class="person-name">DEREK FULHAM</h1>
      <p class="credentials">MSc, CAT(C), RMT, CSCS, Pn2</p>
      <ul class="contact-list">
        <li>
          <svg width="16" height="13" viewBox="0 0 16 13"><rect width="16" height="13" rx="1.5" fill="#2a5fd6"/><path d="M1.5 2 8 7.5 14.5 2" fill="none" stroke="#fff" stroke-width="1.4"/></svg>
          derek@vantrelo.com
        </li>
        <li>
          <svg width="16" height="16" viewBox="0 0 16 16"><circle cx="8" cy="8" r="8" fill="#2a5fd6"/><ellipse cx="8" cy="8" rx="3.2" ry="7" fill="none" stroke="#fff" stroke-width="1.1"/><path d="M1 8h14" stroke="#fff" stroke-width="1.1"/></svg>
          www.vantrelo.com
        </li>
        <li>
          <svg width="16" height="16" viewBox="0 0 16 16"><rect width="16" height="16" rx="3" fill="#2a5fd6"/></svg>
          @derek_fulham
        </li>
      </ul>
    </div>

    <span class="divider"></span>

    <div class="services">
      <h2 class="services-title">SERVICES OFFERED:</h2>
      <ul class="services-list">
        <li><span class="service-bullet"></span>Personal Training</li>
        <li><span class="service-bullet"></span>Golf Fitness</li>
        <li><span class="service-bullet"></span>Injury Rehab</li>
        <li><span class="service-bullet"></span>Massage Therapy</li>
        <li><span class="service-bullet"></span>Yoga</li>
      </ul>
    </div>

    <div class="cta-band">
      <p class="cta">CONTACT US TO RECEIVE A FREE ASSESSMENT</p>
    </div>
  </section>
</main>
</body>
</html>
```